Business Cards for IT Consulting Company (Managed Service Provider)

I am looking to have some business cards printed and would like some designs. We are an IT Consulting company based in Vancouver BC. I would like a nice clean and modern look to the cards. I have uploaded all the versions of my logo so parts can be used as needed. Here is a snippit from our website homepage:

Quillbrook Networks Ltd. is an IT Solutions Partner located in Vancouver BC, Canada. We offer IT solutions and support to customers in the greater Vancouver Area. With expertise in Microsoft platforms, as well as Linux and Mac OSX and over 12 years experience in the IT industry, Quillbrook Networks is dedicated to offering our clients top quality service and products. We take pride in the solutions we offer our customers. The greatest compliment a client can give us is to recommend our services.

Quillbrook Networks Ltd. offers a wide range of IT services from onsite service to remote support and managed service solutions. This allows clients to choose the support path that best suits their company’s needs. Supporting many different sized companies from small to enterprise level over the past 12 years Quillbrook Networks has the experience and expertise needed to ensure things run smoothly. Allowing our clients to focus on doing business.

Reimagining How Modern IT Support Gets Delivered.

Quillbrook Networks is dedicated to providing our clients with IT solutions that work and grow with them for years to come. This philosophy helps save money in the long run instead of replacing equipment constantly. Far too often IT solutions are not well thought out and while possibly solving the problem at hand, require replacement due to growth or quality within a very short time frame. Quillbrook Networks takes pride in providing solutions that will last and be able to accommodate growth without the need for replacement.

Industry/Entity Type

Information Technology

Contact Information for Business Card

Quillbrook Networks Ltd.
(Employee Name)
Eml: (Employees Email Address)
Web: quillbrook.me
Ph: 604-555-0148

Font styles to use
Serif
Sans Serif

Requirements
Must have
• The Company logo and company colors.
Nice to have
• - Our tag line: "Revolutionizing IT Services" or "Reimagining How Modern IT Support Gets Delivered."
• - Also I really like the idea of nature and technology together blending which is sort of where my logo came from so integrating that somehow onto the business cards would be great.

```html
<!DOCTYPE html>
<html lang="en">
<head>
<meta charset="utf-8">
<title>Quillbrook Networks Ltd. — Business Cards</title>
<link rel="stylesheet" href="https://fonts.googleapis.com/css2?family=Open+Sans:wght@400;600;700&display=swap">
<style>
  :root {
    --backdrop: #ecebe8;
    --card-white: #ffffff;
    --brand-blue: #0fa3e0;
    --brand-blue-light: #2bb5ec;
    --brand-blue-deep: #0a8fc9;
    --ink-grey: #5a5f63;
    --soft-grey: #8a8f93;
    --white: #ffffff;
  }
  * { box-sizing: border-box; margin: 0; padding: 0; }
  html, body {
    width: 1200px;
    height: 1023px;
    overflow: hidden;
    background: var(--backdrop);
    font-family: "Open Sans", Arial, sans-serif;
  }
  .canvas { position: relative; width: 1200px; height: 1023px; }

  .card {
    position: absolute;
    border-radius: 4px;
    overflow: hidden;
    box-shadow: 0 6px 18px rgba(0,0,0,.12);
  }

  /* Front */
  .card-front {
    left: 50px; top: 300px;
    width: 600px; height: 343px;
    background: var(--card-white);
  }
  .front-band {
    position: absolute; inset: 0;
    background: var(--brand-blue);
    clip-path: polygon(37% 100%, 37% 60%, 66% 60%, 76% 42%, 100% 42%, 100% 100%);
  }
  .wordmark {
    position: absolute; left: 44px; top: 92px;
    display: flex; align-items: center; gap: 14px;
    color: var(--brand-blue);
    font-weight: 700;
  }
  .wordmark-square {
    width: 38px; height: 38px;
    border: 3px solid var(--brand-blue);
  }
  .wordmark-name { font-size: 44px; line-height: 1; letter-spacing: -0.5px; text-transform: lowercase; }
  .wordmark-sub { font-size: 15px; letter-spacing: 1.5px; line-height: 1.4; text-transform: uppercase; }

  .person { position: absolute; left: 44px; top: 212px; }
  .person-name { font-size: 24px; font-weight: 600; color: var(--brand-blue); }
  .person-name .surname { color: var(--ink-grey); }
  .person-role { font-size: 13px; color: var(--soft-grey); margin-top: 2px; }

  .contact-list {
    position: absolute; left: 240px; top: 236px;
    list-style: none;
    color: var(--white);
    font-size: 15px;
  }
  .contact-list li { display: flex; align-items: center; gap: 10px; height: 26px; }
  .contact-list svg { width: 14px; height: 14px; flex: none; }

  /* Back */
  .card-back {
    left: 760px; top: 200px;
    width: 343px; height: 600px;
    background: linear-gradient(160deg, var(--brand-blue-light), var(--brand-blue) 55%, var(--brand-blue-deep));
  }
  .back-texture { position: absolute; inset: 0; }
  .tagline {
    position: absolute; left: 34px; top: 40px;
    writing-mode: vertical-rl;
    color: var(--white);
    font-size: 15px;
    letter-spacing: 1px;
  }
  .back-mark {
    position: absolute; left: 0; right: 0; top: 262px;
    display: flex; flex-direction: column; align-items: center; gap: 14px;
    color: var(--white);
    font-weight: 700;
    font-size: 30px;
    text-transform: lowercase;
  }
  .back-mark-square { width: 44px; height: 44px; border: 4px solid var(--white); }
</style>
</head>
<body>
<main class="canvas">

  <section class="card card-front" aria-label="Business card front">
    <div class="front-band"></div>

    <div class="wordmark">
      <span class="wordmark-square" aria-hidden="true"></span>
      <div>
        <div class="wordmark-name">quillbrook</div>
        <div class="wordmark-sub">Networks Ltd.</div>
      </div>
    </div>

    <div class="person">
      <div class="person-name">Dana <span class="surname">Whitlow</span></div>
      <div class="person-role">Director</div>
    </div>

    <ul class="contact-list">
      <li>
        <svg viewBox="0 0 16 16" aria-hidden="true"><path fill="#fff" d="M4 1l2.5 3-1.5 2c1 2 3 4 5 5l2-1.5 3 2.5-1.5 2.5C8 15 1 8 1.5 2.5z"/></svg>
        604-555-0148
      </li>
      <li>
        <svg viewBox="0 0 16 16" aria-hidden="true"><rect x="1" y="3" width="14" height="10" fill="#fff"/><path d="M1 3l7 6 7-6" fill="none" stroke="#0fa3e0" stroke-width="1.5"/></svg>
        Employees@quillbrooknetworks.com
      </li>
      <li>
        <svg viewBox="0 0 16 16" aria-hidden="true"><circle cx="8" cy="8" r="7" fill="#fff"/><path d="M1 8h14M8 1c-3 3-3 11 0 14M8 1c3 3 3 11 0 14" fill="none" stroke="#0fa3e0" stroke-width="1.2"/></svg>
        www.quillbrooknetworks.com
      </li>
    </ul>
  </section>

  <section class="card card-back" aria-label="Business card back">
    <div class="back-texture" role="img" aria-label="Faint geometric pattern across the blue card back"></div>
    <p class="tagline">Reimagining How Modern IT Support Gets Delivered.</p>
    <div class="back-mark">
      <span class="back-mark-square" aria-hidden="true"></span>
      <span>quillbrook</span>
    </div>
  </section>

</main>
</body>
</html>
```